International Clinical Software Company needs a new business card design

We are looking for a new business card design for our company that has recently expanded into the UK market, making us a multinational company.
After having rebranded our website and produced a new style guide, we are looking for a business card that is creative and attention grabbing, while being consistent with the style and colour scheme used on the new website, www.plumvora.example
We produce care management technology for the aged care market, but the main aspect we aim to communicate is the human element of our software, and the way it assists in providing better care for aged people, and stronger relationships between aged people and the staff that care for them.
Our current business card is a dark green with gold text, which makes the text quite difficult to read, not very aesthetically appealing and the colour scheme looks quite dated.
We would like something fresh and modern, that can still be colourful but doesn't use large blocks of dark colour, and uses the colours within our logo.
Something tying in with the leaves that are used in our logo could work quite nicely, along with the Autumn/Fall colours of soft greens, yellows and reds (also in our existing logo). However also happy to look at fresh, completely out of the box ideas we may not have yet considered.
Target Market(s)
The people that receive this business card work in the aged card or health industry and are either corporate/management level staff or clinical (Registered Nurses, care workers etc.)
Industry/Entity Type
Health Product
Contact Information for Business Card
Company Name - BrindlewayCare
Company locations: United Kingdom, Australia, New Zealand
Staff Details:
Staff name: Derek Mallow
Staff job title: Executive Chairman
Staff email: d.mallow@plumvora.example
Office phone number: 01742 918576
Font styles to use
Other font styles liked:
- Calibri
Requirements
Must have
- Must include the BrindlewayCare brand name in it's current font
- Must include logo (3 leaves in gold circle)
- Must include Business Card Details
Nice to have
- Elements of gold
- White space
- Something autumn themed but not too cliched
Should not have
- No blue - used by a major competitor and we would like to differentiate from them
- Large blocks of dark green colour (the green that appears in our leaves on the logo on our current business card is the background colour and it is far too dark)

```html
<!DOCTYPE html>
<html lang="en">
<head>
<meta charset="utf-8">
<title>BrindlewayCare business card</title>
<link href="https://fonts.googleapis.com/css2?family=Arimo:wght@400;700&display=swap" rel="stylesheet">
<style>
  :root {
    --backdrop: #3a3a3c;
    --card-white: #ffffff;
    --gold: #bfa87a;
    --gold-dark: #a8925f;
    --text-light: #ffffff;
    --leaf-red: #c9452b;
    --leaf-orange: #e8902a;
    --leaf-yellow: #f2cf3a;
    --leaf-green: #9cb83a;
    --leaf-brown: #7a3a1c;
  }
  * { margin: 0; padding: 0; box-sizing: border-box; }
  html, body { width: 1200px; height: 950px; overflow: hidden; }
  body {
    background: var(--backdrop);
    font-family: "Arimo", Arial, sans-serif;
    position: relative;
  }
  .business-card {
    position: absolute;
    left: 100px; top: 185px;
    width: 1000px; height: 580px;
    background: var(--card-white);
    overflow: hidden;
  }
  .card-art {
    position: absolute; inset: 0;
    width: 1000px; height: 580px;
  }
  .contact-block {
    position: absolute;
    left: 60px; top: 232px;
    color: var(--text-light);
  }
  .staff-name { font-size: 31px; font-weight: 700; line-height: 1.1; }
  .staff-title { font-size: 23px; margin-top: 6px; }
  .locations { font-size: 23px; line-height: 1.4; margin-top: 14px; }
  .contact-list { list-style: none; margin-top: 6px; }
  .contact-list li {
    display: flex; align-items: center; gap: 12px;
    font-size: 23px; line-height: 1.45;
  }
  .contact-icon { width: 20px; height: 20px; flex: none; }
  .brand {
    position: absolute;
    left: 600px; top: 170px;
    width: 380px;
    display: flex; flex-direction: column; align-items: center;
  }
  .brand-mark {
    width: 96px; height: 96px; border-radius: 50%;
    border: 7px solid var(--gold);
  }
  .brand-name {
    margin-top: 22px;
    font-size: 54px; font-weight: 400;
    color: var(--gold);
    letter-spacing: 1px;
  }
  .social-row {
    position: absolute; left: 52px; bottom: 40px;
    display: flex; gap: 8px;
  }
  .social-row span {
    width: 26px; height: 26px; border-radius: 50%;
    background: var(--gold);
  }
</style>
</head>
<body>
  <section class="business-card">
    <svg class="card-art" viewBox="0 0 1000 580" aria-hidden="false">
      <defs>
        <linearGradient id="leafFall" x1="1" y1="0" x2="0" y2="1">
          <stop offset="0" stop-color="var(--leaf-brown)"/>
          <stop offset="0.25" stop-color="var(--leaf-red)"/>
          <stop offset="0.5" stop-color="var(--leaf-orange)"/>
          <stop offset="0.75" stop-color="var(--leaf-yellow)"/>
          <stop offset="1" stop-color="var(--leaf-green)"/>
        </linearGradient>
      </defs>
      <path class="gold-panel" fill="var(--gold)"
            d="M0 0 H560 L520 200 L470 480 H0 Z"/>
      <path class="leaf-cascade" role="img" aria-label="Illustration of colourful autumn leaves cascading down the edge of the gold panel"
            fill="url(#leafFall)" opacity="0.85"
            d="M450 0 H790 C800 60 760 120 700 150 C640 180 600 250 590 320
               C580 390 560 450 520 480 C470 520 380 520 300 515
               C220 512 160 500 130 495 C160 470 260 468 340 462
               C400 456 430 420 440 360 C455 280 430 200 470 140
               C490 100 440 60 450 0 Z"/>
    </svg>

    <div class="contact-block">
      <p class="staff-name">Derek Mallow</p>
      <p class="staff-title">Executive Chairman</p>
      <p class="locations">United Kingdom,<br>Australia, New Zealand</p>
      <ul class="contact-list">
        <li>
          <svg class="contact-icon" viewBox="0 0 20 20"><path fill="#fff" d="M4 2h3l2 5-2 1.5a11 11 0 0 0 4.5 4.5L13 11l5 2v3a2 2 0 0 1-2 2A15 15 0 0 1 2 4a2 2 0 0 1 2-2z"/></svg>
          01742 918576
        </li>
        <li>
          <svg class="contact-icon" viewBox="0 0 20 20"><rect x="1" y="4" width="18" height="12" fill="#fff"/><path d="M1 4l9 7 9-7" fill="none" stroke="var(--gold)" stroke-width="1.6"/></svg>
          d.mallow@plumvora.example
        </li>
        <li>
          <svg class="contact-icon" viewBox="0 0 20 20"><circle cx="10" cy="10" r="9" fill="#fff"/><path d="M1 10h18M10 1c-4 4-4 14 0 18M10 1c4 4 4 14 0 18" fill="none" stroke="var(--gold)" stroke-width="1.2"/></svg>
          www.plumvora.example
        </li>
      </ul>
    </div>

    <div class="brand">
      <span class="brand-mark"></span>
      <p class="brand-name">BrindlewayCare</p>
    </div>

    <div class="social-row"><span></span><span></span><span></span></div>
  </section>
</body>
</html>
```